Etiketten-Design für Dankeswein
Zielgruppe
Kelvora:
Wir stellen für unsere Kunden einen Dankeswein her. Er soll eine Hommage an die Freundschaft und Partnerschaft sein.
Subtitle, could be, but perhaps not:
When we meet, anything can happen.
Name: Kelvora (evtl. Änderung auf Tarnis)
Aufgabenstellung
Das Ettikett darf auch bunt sein, aber es sollte vorallem sehr Professionell sein.
Der Wein wird rötlich sein, die Flasche weiss durchsichtig. Es werden wahrscheinlich 0,5l Flaschen.
Die Form des Ettikets, kann noch definiert werden.
Es geht um eine Homage an das Treffen von Menschen und die Freundschaft.
Kelvora
Hintergrundinfos, die eher für den Hintergrund, Einarbeitung und kleine Abbildung gedacht sind.
PLORAX: ist eine IT Firma, die von 2 Partnern gegründet wurde. Das Logo sollte mit drauf, evtl. kann man auch sich an diesen Farben orientieren.
Familie Dormak: Die Tiersymbole repräsentieren die beiden Eltern. Das geschwungene H ist das Familienzeichen. Wenn man es rotiert. ähnelt es wieder einem Schmetterling. Vielleicht kann man da grafisch etwas machen?
Das geschwungene H oder die Tiersymbole haben hohen emotionalen Wert. In dem Wappen ist das neue Familiensymbol eingearbeitet in das noch ältere Familienwappen der Familie. Prio hat das geschwungene H
Für das Ettikett gibt es leider rechtliche Pflichtangaben:
PLORAX GmbH
Lindauring 14 CH-4057 Basel
Erzeugerab füllung:D- RP 7 348 962
A.P.-Nr.7 348 962 XXXX
11,0%vol 50 cl Enthält Sulfite
Deutscher Qualitätswein – Mosel
kelvora-beispiel.eu

```html
<!DOCTYPE html>
<html lang="de">
<head>
<meta charset="utf-8">
<title>Kelvora – Rotling 2020 Etikett</title>
<link rel="stylesheet" href="https://fonts.googleapis.com/css2?family=Abril+Fatface&family=Montserrat:wght@300;400;500&family=Roboto+Condensed:wght@300;400&display=swap">
<style>
  :root {
    --green: #8bbb15;
    --orange: #f29400;
    --blue: #099dd6;
    --white: #ffffff;
    --ink: #111111;
    --grey: #878787;
    --brand: #3f93c6;
    --page: #ffffff;
  }
  * { margin: 0; padding: 0; box-sizing: border-box; }
  html, body {
    width: 848px;
    height: 1200px;
    overflow: hidden;
    background: var(--page);
  }
  .canvas {
    position: relative;
    width: 848px;
    height: 1200px;
  }
  .label {
    position: absolute;
    left: 44px;
    top: 234px;
    width: 760px;
    height: 732px;
    overflow: hidden;
  }
  .band { position: absolute; left: 0; width: 100%; }
  .band--green-top { top: 0; height: 117px; background: var(--green); }
  .band--orange { top: 117px; height: 97px; background: var(--orange); }
  .band--green-mid { top: 214px; height: 110px; background: var(--green); }
  .band--blue-tag { top: 324px; height: 77px; background: var(--blue); }
  .band--green-tag { top: 401px; height: 79px; background: var(--green); }
  .band--info { top: 480px; height: 162px; background: var(--white); }
  .band--blue-foot { top: 642px; height: 90px; background: var(--blue); }

  .wordmark {
    position: absolute;
    left: 0;
    width: 100%;
    top: 120px;
    text-align: center;
    font-family: "Abril Fatface", serif;
    font-size: 168px;
    line-height: 202px;
    color: var(--white);
    letter-spacing: -2px;
    white-space: nowrap;
  }
  .tagline {
    position: absolute;
    left: 0;
    width: 100%;
    text-align: center;
    font-family: "Montserrat", sans-serif;
    font-weight: 300;
    font-size: 34px;
    letter-spacing: 1.5px;
    color: var(--white);
    line-height: 1;
    white-space: nowrap;
  }
  .tagline--one { top: 360px; }
  .tagline--two { top: 405px; }

  .wine-type {
    position: absolute;
    left: 198px;
    top: 500px;
    font-family: "Montserrat", sans-serif;
    font-weight: 500;
    font-size: 43px;
    letter-spacing: 1.5px;
    color: var(--ink);
    line-height: 1;
    white-space: nowrap;
  }
  .producer {
    position: absolute;
    left: 243px;
    top: 566px;
    font-family: "Montserrat", sans-serif;
    font-weight: 300;
    font-size: 58px;
    letter-spacing: 2px;
    color: var(--brand);
    line-height: 1;
    white-space: nowrap;
  }
  .volume {
    position: absolute;
    left: 611px;
    top: 502px;
    font-family: "Montserrat", sans-serif;
    font-weight: 400;
    font-size: 54px;
    color: var(--grey);
    line-height: 1;
    white-space: nowrap;
  }
  .spec {
    position: absolute;
    left: 615px;
    font-family: "Roboto Condensed", sans-serif;
    font-weight: 300;
    font-size: 21px;
    letter-spacing: -0.3px;
    color: var(--grey);
    line-height: 1;
    white-space: nowrap;
  }
  .spec--alcohol { top: 558px; }
  .spec--sulfites { top: 606px; }

  .bottler {
    position: absolute;
    left: 0;
    width: 100%;
    top: 698px;
    text-align: center;
    font-family: "Roboto Condensed", sans-serif;
    font-weight: 400;
    font-size: 22px;
    color: var(--white);
    line-height: 1;
    white-space: nowrap;
  }
</style>
</head>
<body>
  <main class="canvas">
    <section class="label" aria-label="Weinetikett Kelvora Rotling 2020">
      <div class="band band--green-top"></div>
      <div class="band band--orange"></div>
      <div class="band band--green-mid"></div>
      <div class="band band--blue-tag"></div>
      <div class="band band--green-tag"></div>
      <div class="band band--info"></div>
      <div class="band band--blue-foot"></div>

      <h1 class="wordmark">Kelvora</h1>

      <p class="tagline tagline--one">WHEN WE MEET,</p>
      <p class="tagline tagline--two">ANYTHING CAN HAPPEN</p>

      <p class="wine-type">ROTLING - 2020</p>
      <p class="producer">PLORAX</p>
      <p class="volume">0,5 l</p>
      <p class="spec spec--alcohol">13% vol.</p>
      <p class="spec spec--sulfites">enthält Sulfite</p>

      <p class="bottler">Abfüllung: Herstelleradresse, Weingut, Straße Nr. 0, 0000 Stadt</p>
    </section>
  </main>
</body>
</html>
```